Brochure design for International Beauty Trade Show

I neee a tri-fold company products' brochure to distribute to customers at an international trade show coming soon. We have 4 main product categories- hair and skincare, facial care, Body and bath and massage oil.
The brochure needs to include at least 2 photos of the main products of each category, benefits, call to action and our company contact info ( website and phone number).

Target Market(s)

Educated and high income earners looking for all-natural,pure, 100 organic products for their beauty and personal care needs. Our products cross all racial groups/demographics and suitable for all skin types

Industry/Entity Type

Hair And Beauty

Font styles to use
Serif

Colors

Designer to choose colors to be used in the design.

Requirements
Must have
• The design must stand out as pure and luxury and at the same time be inclusive using our logo design colors- orange and blue. Also, the content must be easy to read and captivating.
• Finally if using women pictures, please include Black, white, Asian and Latina to reflect the fact that our products are suitable for all skin types.
Nice to have
• Design the brochure such that it could be printed as a poster-banner ad.
Should not have
• Cookie cutter designs are not welcome

```html
<!DOCTYPE html>
<html lang="en">
<head>
<meta charset="utf-8">
<title>Solvanta – Natural Solutions Brochure</title>
<link href="https://fonts.googleapis.com/css2?family=Lora:wght@400;500;700&display=swap" rel="stylesheet">
<style>
  :root {
    --blue: #1a8fc8;
    --orange: #ef7125;
    --ink: #3a3a3a;
    --paper: #ffffff;
    --backdrop: #e6e6e6;
    --photo-a: #c9c4c0;
    --photo-b: #8a6a55;
    --prod-warm: #e9c9a4;
    --prod-cream: #efe4d4;
    --prod-sage: #c9d3b8;
    --prod-amber: #d8a46a;
  }
  * { margin: 0; padding: 0; box-sizing: border-box; }
  html, body { width: 1200px; height: 1000px; overflow: hidden; }
  body {
    background: var(--backdrop);
    font-family: "Lora", Georgia, serif;
    position: relative;
  }
  .brochure {
    position: absolute;
    left: 70px; top: 92px;
    width: 1070px; height: 828px;
    background: var(--paper);
    box-shadow: 0 2px 10px rgba(0,0,0,0.15);
    overflow: hidden;
  }
  .bands { position: absolute; left: 0; top: 0; width: 708px; height: 828px; }
  .mission {
    position: absolute; left: 25px; top: 126px; width: 312px;
    font-size: 16px; line-height: 22.5px; color: var(--ink);
    text-align: justify;
  }
  .range-intro {
    position: absolute; left: 25px; top: 281px; width: 320px;
    font-size: 15px; line-height: 21px; color: var(--ink);
  }
  .product-list {
    position: absolute; left: 33px; top: 332px; list-style: none;
  }
  .product-list li {
    font-size: 16.5px; color: var(--ink);
    height: 32px; line-height: 22px; padding-left: 19px; position: relative;
  }
  .product-list li::before {
    content: ""; position: absolute; left: 0; top: 6px;
    width: 10px; height: 10px; border-radius: 50%; background: var(--blue);
  }
  .categories {
    position: absolute; left: 382px; top: 146px; width: 300px;
    display: grid; grid-template-columns: 1fr 1fr; gap: 14px 16px;
  }
  .category-photos { display: flex; gap: 4px; height: 78px; }
  .category-photos span { flex: 1; border-radius: 3px; }
  .category-name {
    margin-top: 6px; font-size: 13px; font-weight: 700; color: var(--blue);
    text-align: center; line-height: 16px;
  }
  .tone-warm { background: linear-gradient(160deg, var(--prod-cream), var(--prod-warm)); }
  .tone-amber { background: linear-gradient(160deg, var(--prod-warm), var(--prod-amber)); }
  .tone-sage { background: linear-gradient(160deg, var(--prod-cream), var(--prod-sage)); }
  .brand-mark {
    position: absolute; display: flex; align-items: center; justify-content: center; gap: 10px;
    color: var(--orange); font-weight: 700;
  }
  .brand-mark .dot { border-radius: 50%; background: var(--blue); flex: none; }
  .brand-mark--cover { left: 708px; top: 150px; width: 362px; font-size: 44px; }
  .brand-mark--cover .dot { width: 22px; height: 22px; }
  .brand-mark--back { left: 372px; top: 432px; width: 320px; font-size: 34px; }
  .brand-mark--back .dot { width: 18px; height: 18px; }
  .order {
    position: absolute; left: 372px; top: 575px; width: 320px; text-align: center;
  }
  .order-title {
    font-size: 21px; font-weight: 700; color: var(--blue); letter-spacing: 1.5px;
  }
  .order-line {
    font-size: 21px; color: var(--ink); line-height: 29px; letter-spacing: 0.5px;
  }
  .order-title + .order-line { margin-top: 20px; }
  .order-phone {
    font-size: 36px; font-weight: 700; color: var(--orange); margin-top: 6px;
  }
  .cover-title {
    position: absolute; left: 708px; top: 272px; width: 362px; text-align: center;
  }
  .cover-title .headline {
    font-size: 25px; font-weight: 700; color: var(--blue); line-height: 30px;
  }
  .cover-title .tagline {
    font-size: 25px; color: var(--orange); line-height: 36px;
  }
  .cover-photo {
    position: absolute; left: 708px; top: 404px; width: 362px; height: 424px;
    background: linear-gradient(160deg, var(--photo-a) 0%, var(--photo-b) 100%);
  }
</style>
</head>
<body>
  <main class="brochure">
    <svg class="bands" viewBox="0 0 708 828" aria-hidden="true">
      <polygon points="0,0 708,0 708,127 0,28" fill="var(--blue)"/>
      <polygon points="0,706 708,803 708,828 0,828" fill="var(--orange)"/>
    </svg>

    <p class="mission">Our mission is to satisfy our customers by supplying them with pure, natural and 100% organic products, which make them more attractive and solve the most common skin and hair problems.</p>

    <p class="range-intro">Over 20 luxury Products to choose from including:</p>
    <ul class="product-list">
      <li>Argan oil</li>
      <li>Moroccan Beldi Soaps</li>
      <li>Prickly Pear seed oil</li>
      <li>Shea Butter</li>
      <li>Carrot oil</li>
      <li>Green Clay Mask</li>
      <li>Castor oil</li>
      <li>Stretch marks/vergeture oil</li>
      <li>Massage oil</li>
      <li>Black Soaps</li>
    </ul>

    <section class="categories">
      <div class="category">
        <div class="category-photos">
          <span class="tone-amber" role="img" aria-label="Product photo: argan oil bottle"></span>
          <span class="tone-warm" role="img" aria-label="Product photo: shea butter jar"></span>
        </div>
        <p class="category-name">Hair &amp; Skincare</p>
      </div>
      <div class="category">
        <div class="category-photos">
          <span class="tone-sage" role="img" aria-label="Product photo: green clay mask jar"></span>
          <span class="tone-amber" role="img" aria-label="Product photo: prickly pear seed oil bottle"></span>
        </div>
        <p class="category-name">Facial Care</p>
      </div>
      <div class="category">
        <div class="category-photos">
          <span class="tone-warm" role="img" aria-label="Product photo: Moroccan beldi soap"></span>
          <span class="tone-sage" role="img" aria-label="Product photo: black soap bar"></span>
        </div>
        <p class="category-name">Body &amp; Bath</p>
      </div>
      <div class="category">
        <div class="category-photos">
          <span class="tone-amber" role="img" aria-label="Product photo: massage oil bottle"></span>
          <span class="tone-warm" role="img" aria-label="Product photo: stretch marks oil bottle"></span>
        </div>
        <p class="category-name">Massage Oil</p>
      </div>
    </section>

    <div class="brand-mark brand-mark--back"><span class="dot"></span>Solvanta</div>

    <div class="order">
      <p class="order-title">ORDER NOW AT:</p>
      <p class="order-line">www.solvanta.com</p>
      <p class="order-line">info@solvanta.com</p>
      <p class="order-phone">(800) 555-0142</p>
    </div>

    <div class="brand-mark brand-mark--cover"><span class="dot"></span>Solvanta</div>

    <div class="cover-title">
      <p class="headline">NATURAL SOLUTIONS</p>
      <p class="tagline">to Forever Beauty</p>
    </div>

    <div class="cover-photo" role="img" aria-label="Photo of a smiling woman with curly hair touching her hair"></div>
  </main>
</body>
</html>
```